Need Primer (paint) Label Design

THE ATTACHED LABEL/S ARE SOLEY FOR REFERENCE. DO NOT MAKE ME AN INTERIOR PAINT OR CHALK PAINT LABEL. I ONLY NEED A "PRIMER" LABEL. THE ATTACHED INTERIOR PAINT LABEL IS ONLY TO SHOW YOU THE THEME/DESIGN OF OUR OTHER LABELS. THE BLUE LABEL ONLY HAS A DESIGN ASPECT I LIKE (PRIMER ON SIDE). The last four labels are our competitors.
```````````````````````````````````````````````````````````````````````````````````````````````````
We need this label to look professional, sharp, eye catching and modern.
OUR PRIMARY COLORS ARE BLACK AND WHITE. IF YOU INCOPORATE ANOTHER COLOR, SILVER OR GOLD MIGHT BE IDEAL BUT PLEASE DON'T DRIFT TOO FAR.
The attached documents:
1st - Our Logo
2nd - Our chalk paint label (reference). We do not need a chalk paint label.
3rd. A random design example. I like the PRIME on the side running vertically. I think it's a cool design concept.
````````````````````````````````````````````````````````````````````````````````````````````````````
We are going to be using a normal paint can with a metal bail/handle so please use that with you design work
``````````````````````````````````````````````````````````````````````````````````````````````````
Order, in my head:
4376
Coatings
^^ I want this to stand out as well but I don't want it to be the first thing your eye is drawn to. Probably 2nd
Interior/Exterior
Multi - Surface Primer
^^ Want this to stick out and draw your eye so the customer knows what it is immediately
Exceptional Adhesion, Performance, Durability,
Use on Wood, Drywall, Plaster, Stucco, Masonry, Brick, Paneling, Painted Metal, & Properly Prepared Glossy Surfaces & More
35* Lowe Temperature Application (can be on side or small)
100% Acrylic
Low Odor - Low VOC - Soap & Water Clean Up
1 US Gallon - 3.785 L
Feel free to get creative with it!

```html
<!DOCTYPE html>
<html lang="en">
<head>
<meta charset="utf-8">
<title>4376 Coatings – Multi-Surface Primer Label</title>
<link rel="stylesheet" href="https://fonts.googleapis.com/css2?family=Montserrat:wght@300;700;800&family=Open+Sans:wght@400&display=swap">
<style>
  :root {
    --ink: #000000;
    --label: #050505;
    --paper: #ffffff;
    --backdrop: #e6e6e6;
    --silver-light: #d8d8d8;
    --silver-mid: #8a8a8a;
    --panel-dark: #1a1a1a;
  }
  * { margin: 0; padding: 0; box-sizing: border-box; }
  html, body {
    width: 1200px; height: 552px; overflow: hidden;
    background: var(--backdrop);
  }
  .label {
    position: absolute; left: 395px; top: 16px;
    width: 411px; height: 520px;
    background: var(--label);
    color: var(--paper);
    font-family: "Open Sans", Arial, sans-serif;
    overflow: hidden;
    box-shadow: 0 10px 14px -8px rgba(0,0,0,0.35);
  }
  .title-glow {
    position: absolute; left: 288px; top: 0; width: 104px; height: 170px;
    background: linear-gradient(180deg, var(--panel-dark) 0%, var(--label) 100%);
  }
  .brand { position: absolute; left: 0; top: 0; width: 240px; height: 170px; }
  .brand-text { font-family: "Montserrat", sans-serif; font-weight: 300; fill: var(--paper); }
  .brand-number { font-size: 118px; }
  .brand-word { font-size: 33px; }

  .finish-band {
    position: absolute; left: 0; top: 176px; width: 209px; height: 21px;
    background: linear-gradient(90deg, var(--silver-light) 0%, var(--silver-mid) 30%, #2a2a2a 65%, var(--ink) 100%);
    border-top: 1px solid var(--silver-mid); border-bottom: 1px solid var(--silver-mid);
    font-family: "Montserrat", sans-serif; font-weight: 800; font-size: 13px;
    line-height: 19px; padding-left: 27px; letter-spacing: 0.2px; white-space: nowrap;
  }
  .benefits { position: absolute; left: 27px; top: 213px; list-style: none; font-size: 12px; line-height: 15.6px; }
  .benefits li { display: flex; align-items: center; gap: 6px; }
  .benefits svg { width: 8px; height: 8px; }

  .tag-band {
    position: absolute; left: 0; height: 13px; width: 84px;
    background: linear-gradient(90deg, var(--paper) 0%, var(--paper) 60%, rgba(255,255,255,0) 100%);
    color: var(--ink); font-size: 10.5px; line-height: 13px; padding-left: 27px;
  }
  .uses-band { top: 287px; }
  .uses-list {
    position: absolute; left: 28px; top: 299px; width: 230px;
    display: grid; grid-template-columns: 53px 72px 60px;
    font-size: 9.2px; line-height: 14.6px; list-style: none;
  }
  .uses-list li::before { content: "■"; font-size: 5px; vertical-align: 2px; margin-right: 3px; }
  .uses-list .wide { grid-column: 1 / 4; margin-top: 1px; }

  .temp { position: absolute; left: 27px; top: 379px; display: flex; align-items: flex-start; gap: 2px; }
  .temp svg { width: 8px; height: 18px; }
  .temp-value { font-family: "Montserrat", sans-serif; font-weight: 700; font-size: 10px; line-height: 10px; }
  .temp-note { display: block; font-size: 4.3px; line-height: 6px; font-weight: 400; font-family: "Open Sans", sans-serif; white-space: nowrap; }
  .acrylic { position: absolute; left: 120px; top: 379px; font-size: 13px; white-space: nowrap; }
  .acrylic b { font-family: "Montserrat", sans-serif; font-weight: 700; }

  .features {
    position: absolute; left: 27px; top: 416px; display: flex;
    border: 1px solid var(--paper); font-size: 7.6px; line-height: 11px; white-space: nowrap;
  }
  .features span { padding: 0 5px; }
  .features span + span { border-left: 1px solid var(--paper); }

  .volume-band { top: 459px; font-size: 8.5px; width: 90px; }
  .volume { position: absolute; left: 27px; top: 474px; font-family: "Montserrat", sans-serif; font-weight: 300; font-size: 25px; letter-spacing: 0.5px; }

  .product-title { position: absolute; left: 0; top: 0; width: 411px; height: 520px; }
  .product-type { font-family: "Montserrat", sans-serif; font-weight: 300; font-size: 44px; fill: var(--paper); }
  .product-name { font-family: "Montserrat", sans-serif; font-weight: 700; font-size: 128px; fill: var(--paper); }
</style>
</head>
<body>
  <main class="label">
    <div class="title-glow"></div>

    <svg class="brand" viewBox="0 0 240 170" aria-label="4376 Coatings">
      <text class="brand-text brand-number" x="29" y="121" textLength="181" lengthAdjust="spacingAndGlyphs">4376</text>
      <text class="brand-text brand-word" x="29" y="159" textLength="179" lengthAdjust="spacing">COATINGS</text>
    </svg>

    <div class="finish-band">INTERIOR -EXTERIOR</div>

    <ul class="benefits">
      <li><svg viewBox="0 0 8 8"><rect x="0.5" y="0.5" width="7" height="7" fill="none" stroke="#fff"/><path d="M1.8 4 L3.5 5.8 L7.5 0.8" fill="none" stroke="#fff" stroke-width="1"/></svg>Exceptional Adhesion</li>
      <li><svg viewBox="0 0 8 8"><rect x="0.5" y="0.5" width="7" height="7" fill="none" stroke="#fff"/><path d="M1.8 4 L3.5 5.8 L7.5 0.8" fill="none" stroke="#fff" stroke-width="1"/></svg>Performance</li>
      <li><svg viewBox="0 0 8 8"><rect x="0.5" y="0.5" width="7" height="7" fill="none" stroke="#fff"/><path d="M1.8 4 L3.5 5.8 L7.5 0.8" fill="none" stroke="#fff" stroke-width="1"/></svg>Durability</li>
    </ul>

    <div class="tag-band uses-band">Uses</div>
    <ul class="uses-list">
      <li>Wood</li><li>Drywall</li><li>Plaster</li>
      <li>Stucco</li><li>Masonry</li><li>Brick</li>
      <li>Paneling</li><li>Painted Metal</li>
      <li class="wide">Properly Prepared Glossy Surfaces &amp; More...</li>
    </ul>

    <div class="temp">
      <svg viewBox="0 0 8 18"><rect x="2" y="0.5" width="4" height="12" rx="2" fill="none" stroke="#fff" stroke-width="0.8"/><circle cx="4" cy="14.5" r="3" fill="none" stroke="#fff" stroke-width="0.8"/><line x1="4" y1="6" x2="4" y2="14" stroke="#fff" stroke-width="1.2"/></svg>
      <span class="temp-value">35°<span class="temp-note">Low Temperature Application</span></span>
    </div>
    <div class="acrylic"><b>100%</b> Acrylic</div>

    <div class="features"><span>Low Odor</span><span>Low VOC</span><span>Soap &amp; Water Clean Up</span></div>

    <div class="tag-band volume-band">1 US Gallon</div>
    <div class="volume">3.785 L</div>

    <svg class="product-title" viewBox="0 0 411 520">
      <text class="product-type" transform="translate(277 499) rotate(-90)" textLength="325" lengthAdjust="spacingAndGlyphs">MULTI - SURFACE</text>
      <text class="product-name" transform="translate(381 499) rotate(-90)" textLength="461" lengthAdjust="spacingAndGlyphs">PRIMER</text>
    </svg>
  </main>
</body>
</html>
```